Candle Box & Belly Band Design

Design Candle Box for Soy Candles along with a belly band design that can be used on off the shelf coloured boxes. It is for a premium brand of candle - so i want the packaging to reflect this. I have included must haves below.

The candle boxes will be a few different sizes, but for the purpose of the design it would be something like a cube 12 x 12 x 12 cms

The belly band for standard boxes to be something like 5cm wide on a 12 x 12 x 12cms cube box that goes all the way around the top to the bottom - holding the lid on and providing all the relevant information. Example of box with belly band uploaded

Our company Name : Clover & Jude - our logo is uploaded

Target Market(s)

Premium Candle Buyers

Colors

Designer to choose colors to be used in the design.

Requirements
Must have
• Must have our logo - our logo can be in any colour
• Must state:
• Soy Candle, Hand Poured, Made in Melbourne,
• A space for the fragrance, size and burn time.
• For this project use Lime, Coconut & Elderfllower, 300grams, 50 Hour burn Time

```html
<!DOCTYPE html>
<html lang="en">
<head>
<meta charset="utf-8">
<title>Clover &amp; Jude Soy Candle Belly Band</title>
<link rel="stylesheet" href="https://fonts.googleapis.com/css2?family=Oswald:wght@300;400&family=Open+Sans:wght@400;600&display=swap">
<style>
  :root {
    --page: #ececec;
    --band: #000000;
    --silver: #c9c9c9;
    --strip: #d6d6d6;
    --ink: #111111;
  }
  * { box-sizing: border-box; margin: 0; padding: 0; }
  html, body { width: 1200px; height: 923px; overflow: hidden; }
  body {
    background: var(--page);
    display: flex;
    align-items: center;
    justify-content: center;
  }
  .belly-band {
    width: 320px;
    height: 800px;
    background: var(--band);
    display: flex;
    flex-direction: column;
    align-items: center;
    padding: 14px 0;
  }
  .band-strip {
    width: 100%;
    height: 24px;
    background: var(--strip);
    color: var(--ink);
    font-family: "Oswald", sans-serif;
    font-weight: 400;
    font-size: 14px;
    line-height: 24px;
    white-space: nowrap;
    overflow: hidden;
    text-align: center;
    letter-spacing: 0.2px;
  }
  .brand {
    margin-top: 48px;
    display: flex;
    flex-direction: column;
    align-items: center;
    gap: 22px;
  }
  .brand-dot {
    width: 70px;
    height: 70px;
    border-radius: 50%;
    background: var(--silver);
  }
  .brand-name {
    font-family: "Open Sans", sans-serif;
    font-weight: 400;
    font-size: 24px;
    color: var(--silver);
  }
  .product-title {
    margin-top: 44px;
    font-family: "Oswald", sans-serif;
    font-weight: 300;
    font-size: 80px;
    line-height: 0.98;
    color: var(--silver);
    text-align: center;
  }
  .fragrance {
    margin-top: 4px;
    font-family: "Open Sans", sans-serif;
    font-weight: 400;
    font-size: 28px;
    line-height: 1.18;
    letter-spacing: 3px;
    color: var(--silver);
    text-align: center;
  }
  .details {
    margin-top: auto;
    margin-bottom: 26px;
    font-family: "Oswald", sans-serif;
    font-weight: 300;
    color: var(--silver);
    text-align: center;
  }
  .burn-time {
    display: flex;
    align-items: center;
    justify-content: center;
    gap: 3px;
    font-size: 19px;
  }
  .burn-time svg { width: 14px; height: 18px; }
  .weight { font-size: 24px; margin-top: 2px; }
</style>
</head>
<body>
  <main class="belly-band">
    <div class="band-strip">HAND POURED • HAND POURED • HAND POURED • HAND POURED</div>

    <div class="brand">
      <span class="brand-dot"></span>
      <span class="brand-name">Clover &amp; Jude</span>
    </div>

    <h1 class="product-title">Soy<br>Candle</h1>
    <p class="fragrance">Lime, Coconut<br>&amp; Elderflower</p>

    <div class="details">
      <p class="burn-time">
        <svg viewBox="0 0 14 18" aria-hidden="true">
          <path d="M7 0C8 4 13 6 13 11.5A6 6 0 0 1 1 11.5C1 8.5 3 7 4 5c.5 2 1.5 3 2.5 3C7.5 6 6 3 7 0Z" fill="#c9c9c9"/>
        </svg>
        50 Hour burn Time
      </p>
      <p class="weight">300 gr</p>
    </div>

    <div class="band-strip">RNE• MADE IN MELBOURNE• MADE IN MELBOURNE • MA</div>
  </main>
</body>
</html>
```